Business cards for a fun web development agency

Hi,I am building a web development agency. You can read about it on the website http://kite-loft.examplehost.com. Basically, I want to focus on free and open source products and stay as far away from the corporate business feeling as possible. I want to build a community so I want the business card to feel fun and approachable (at the risk of professional if need be). I am uploading some of my image assets in various file formats. Feel free to use them or make your own if you want just keeping in theme with the website.
Industry/Entity Type
Building
Contact Information for Business Card
Company Name: Boat ShedWebsite: www.kiteloftdev.example (it's currently in alpha on http://kite-loft.examplehost.com if you want to see the them we are trying to capture)My name is: Banner B. SchaferMy email: banner@boatsheddev.comMy phone: 0431 587 904
Look and feel

```html
<!DOCTYPE html>
<html lang="en">
<head>
<meta charset="utf-8">
<title>Kite Loft — Business Card</title>
<link rel="stylesheet" href="https://fonts.googleapis.com/css2?family=Arimo:wght@400;700&display=swap">
<style>
  :root {
    --page-bg: #e9e6e1;
    --paper: #ffffff;
    --teal: #2ab3cf;
    --teal-light: #3fc4dd;
    --teal-deep: #1490ad;
    --brand: #1d9fbf;
    --ink-light: #ffffff;
    --scene-pale: #cfe7ec;
    --scene-mid: #9fcfdb;
  }
  * { box-sizing: border-box; margin: 0; padding: 0; }
  html, body { width: 1200px; height: 885px; overflow: hidden; }
  body {
    background: var(--page-bg);
    font-family: "Arimo", Arial, sans-serif;
    display: flex;
    flex-direction: column;
    align-items: center;
    justify-content: center;
    gap: 56px;
  }
  .card {
    width: 620px;
    height: 354px;
    position: relative;
    overflow: hidden;
    box-shadow: 0 10px 24px rgba(0,0,0,0.18);
  }

  /* Front */
  .card-front { background: var(--paper); }
  .front-brand {
    height: 56%;
    display: flex;
    align-items: center;
    justify-content: center;
    gap: 18px;
  }
  .brand-name {
    color: var(--brand);
    font-weight: 400;
    font-size: 64px;
    letter-spacing: 1px;
    text-transform: uppercase;
    white-space: nowrap;
  }
  .brand-dot {
    width: 60px; height: 60px;
    border-radius: 50%;
    background: var(--brand);
    flex: none;
  }
  .front-band {
    position: absolute;
    left: 0; right: 0; bottom: 0;
    height: 44%;
    background: linear-gradient(180deg, var(--teal-light), var(--teal));
    display: flex;
    align-items: center;
    padding: 0 34px;
    color: var(--ink-light);
  }
  .holder-name {
    font-size: 26px;
    font-weight: 400;
    width: 250px;
    white-space: nowrap;
  }
  .band-divider {
    width: 1.5px;
    height: 92px;
    background: var(--ink-light);
    margin: 0 22px 0 6px;
    flex: none;
  }
  .contact-list { list-style: none; font-size: 17px; line-height: 1.6; white-space: nowrap; }
  .contact-list li { display: flex; align-items: center; gap: 9px; }
  .contact-icon {
    width: 17px; height: 17px;
    border-radius: 3px;
    background: var(--ink-light);
    display: flex; align-items: center; justify-content: center;
    flex: none;
  }

  /* Back */
  .card-back {
    background: radial-gradient(ellipse at 60% 40%, var(--teal) 0%, var(--teal-deep) 100%);
  }
  .back-scene {
    position: absolute;
    left: 268px; top: 58px;
    width: 206px; height: 206px;
    border-radius: 50%;
    border: 4px solid var(--paper);
    background: radial-gradient(circle at 60% 40%, var(--scene-pale), var(--scene-mid));
  }
  .back-url {
    position: absolute;
    left: 40px; bottom: 42px;
    display: flex; align-items: center; gap: 16px;
    color: var(--ink-light);
    font-size: 18px;
    white-space: nowrap;
  }
  .back-url .rule {
    width: 110px; height: 1.5px;
    background: var(--ink-light);
  }
</style>
</head>
<body>

  <section class="card card-front">
    <div class="front-brand">
      <span class="brand-name">Kite Loft</span>
      <span class="brand-dot" aria-hidden="true"></span>
    </div>
    <div class="front-band">
      <p class="holder-name">Corwin T. Aldous</p>
      <span class="band-divider" aria-hidden="true"></span>
      <ul class="contact-list">
        <li>
          <span class="contact-icon" aria-hidden="true">
            <svg width="11" height="11" viewBox="0 0 24 24"><path fill="#2ab3cf" d="M6.6 10.8a15 15 0 0 0 6.6 6.6l2.2-2.2a1 1 0 0 1 1-.25 11.4 11.4 0 0 0 3.6.57 1 1 0 0 1 1 1V20a1 1 0 0 1-1 1A17 17 0 0 1 3 4a1 1 0 0 1 1-1h3.5a1 1 0 0 1 1 1c0 1.25.2 2.45.57 3.57a1 1 0 0 1-.25 1z"/></svg>
          </span>0431 587 904
        </li>
        <li>
          <span class="contact-icon" aria-hidden="true">
            <svg width="12" height="12" viewBox="0 0 24 24" fill="none" stroke="#2ab3cf" stroke-width="2"><circle cx="12" cy="12" r="9"/><path d="M3 12h18M12 3c3 3.5 3 14.5 0 18M12 3c-3 3.5-3 14.5 0 18"/></svg>
          </span>www.kiteloftdev.example
        </li>
        <li>
          <span class="contact-icon" aria-hidden="true">
            <svg width="12" height="12" viewBox="0 0 24 24" fill="none" stroke="#2ab3cf" stroke-width="2"><rect x="3" y="6" width="18" height="12"/><path d="M3 6l9 7 9-7"/></svg>
          </span>corwin@kiteloftdev.example
        </li>
      </ul>
    </div>
  </section>

  <section class="card card-back">
    <div class="back-scene" role="img" aria-label="Circular illustration of a small blue cabin at the end of a jetty over calm water"></div>
    <p class="back-url">www.kiteloftdev.example<span class="rule" aria-hidden="true"></span></p>
  </section>

</body>
</html>
```